Party Favors and Decorations Business Needs A Business Card Design

We are in need of a Logo design and business card design for a new small business called Bright Lantern Designs. We create party decorations and favours for Bridal Showers, Baby Showers, Weddings Birthdays etc. This is a very personalized service based on Clients theme, colour, and style. We are looking for a high end elegant look. I have attached a file to the style I like including the type of paper.

Target Market(s)

women, young adults, expectant mothers, mothers

Industry/Entity Type

Small Business

Contact Information for Business Card

Bright Lantern Designs Essex, ON 519-847-2061 brightlanterndesigns.ca karen@brightlanterngiftbox.com find us on Chatterly

Logo Text

Bright Lantern Designs

Font styles to use
Script

Requirements
Must have
• Name, email, web address, phone number
Should not have
• cutesy graphics

```html
<!DOCTYPE html>
<html lang="en">
<head>
<meta charset="utf-8">
<title>Bright Lantern Designs – Business Card</title>
<link rel="stylesheet" href="https://fonts.googleapis.com/css2?family=Cabin:wght@400;600;700&family=Courgette&display=swap">
<style>
  :root {
    --ink: #111111;
    --paper: #ffffff;
    --paper-shade: #e9e9e9;
    --backdrop: #d8d4cc;
    --light-text: #f2f2f2;
    --text-font: "Cabin", Arial, sans-serif;
    --script-font: "Courgette", cursive;
  }
  * { box-sizing: border-box; margin: 0; padding: 0; }
  html, body { width: 1200px; height: 885px; overflow: hidden; }
  body {
    background: var(--backdrop);
    display: flex;
    align-items: center;
    justify-content: center;
    gap: 70px;
    font-family: var(--text-font);
  }
  .card {
    width: 400px;
    height: 700px;
    border-radius: 4px;
    box-shadow: 0 10px 28px rgba(0,0,0,.28);
    overflow: hidden;
    display: flex;
    flex-direction: column;
    align-items: center;
  }

  /* Front */
  .card--front {
    background: linear-gradient(180deg, var(--paper) 0%, var(--paper) 60%, var(--paper-shade) 100%);
    color: var(--ink);
  }
  .front__body {
    flex: 1;
    width: 100%;
    display: flex;
    flex-direction: column;
    align-items: center;
    text-align: center;
    padding-top: 70px;
  }
  .brand-name {
    font-family: var(--text-font);
    font-weight: 600;
    font-size: 34px;
    line-height: 1.1;
    letter-spacing: .5px;
  }
  .card--front .brand-name { color: var(--ink); }
  .employee-name {
    font-family: var(--script-font);
    font-size: 38px;
    margin-top: 46px;
  }
  .services__title {
    font-weight: 700;
    font-size: 27px;
    margin-top: 22px;
    letter-spacing: .5px;
  }
  .services__list {
    list-style: none;
    font-size: 21px;
    line-height: 1.2;
    margin-top: 6px;
    letter-spacing: .5px;
  }
  .phone {
    font-weight: 700;
    font-size: 34px;
    letter-spacing: 2px;
    margin-top: 26px;
  }
  .email {
    font-size: 20px;
    margin-top: 10px;
    letter-spacing: .3px;
  }
  .social {
    display: flex;
    align-items: center;
    gap: 10px;
    margin-top: 22px;
  }
  .social__mark {
    width: 26px;
    height: 26px;
    background: var(--ink);
    border-radius: 3px;
  }
  .social__name {
    font-weight: 700;
    font-size: 24px;
  }
  .social__lead {
    font-size: 14px;
    font-weight: 600;
  }
  .front__band {
    width: 100%;
    height: 96px;
    background: var(--ink);
    color: var(--light-text);
    display: flex;
    align-items: center;
    justify-content: center;
    font-size: 29px;
    font-weight: 600;
    letter-spacing: 1.5px;
  }

  /* Back */
  .card--back {
    background: var(--ink);
    color: var(--light-text);
    justify-content: flex-start;
    padding-top: 230px;
    text-align: center;
  }
  .card--back .brand-name { color: var(--light-text); }
  .back__web {
    margin-top: 40px;
    font-size: 27px;
    font-weight: 600;
    letter-spacing: 1.5px;
  }
</style>
</head>
<body>
  <article class="card card--front">
    <div class="front__body">
      <div class="brand-name">Bright Lantern Designs</div>
      <div class="employee-name">Employee Name</div>
      <h2 class="services__title">Our Services</h2>
      <ul class="services__list">
        <li>Gift Wrapping Occasions</li>
        <li>Wrapping Service Pricing</li>
        <li>Packaging Pricing</li>
        <li>Gifts, Packaging &amp; Wrapping</li>
      </ul>
      <div class="phone">519-847-2061</div>
      <div class="email">karen@brightlanterngiftbox.com</div>
      <div class="social">
        <span class="social__mark" aria-hidden="true"></span>
        <span class="social__lead">Find us on</span>
        <span class="social__name">Chatterly</span>
      </div>
    </div>
    <div class="front__band">brightlanterndesigns.ca</div>
  </article>

  <article class="card card--back">
    <div class="brand-name">Bright Lantern Designs</div>
    <div class="back__web">brightlanterndesigns.ca</div>
  </article>
</body>
</html>
```